Computer Company needs a Business card design

We need a business card design for our business. We assist people to transition to the KVS (Kestrel Vantage Scheme). The Verandal Crown Office-owned kvs™ network is a brand new telecommunications network currently being rolled out across Australia, giving access to a reliable broadband connection. Our niche market will predominantly be domestic customers in the 50+ age bracket. The assistance that we provide is everything from arranging the equipment, arranging the plan and contract term, appointment times, final testing of the network and any tweaks that need to be made. We basically PM the transition from start to finish. The business card design should be minimalist, should communicate loyalty and stability, should be easy to read and clearly explain what we do. We have asked for front and back. However, the back of the card does not have to include much information at all. It could be just a small design, or a repeat of our phone number. Up to you. The attached file only says what is required on the card. It does not specify where to arrange the text, what fonts to use, etc etc. As much as we would like to give you more info, due to our very limited design ability, we are not really able to send you any rough, or otherwise, designs of what we are after. Hopefully the above description is enough for you.

```html
<!DOCTYPE html>
<html lang="en">
<head>
<meta charset="utf-8">
<title>Harbourline Connect – Business Card</title>
<link href="https://fonts.googleapis.com/css2?family=Lato:wght@400;700&display=swap" rel="stylesheet">
<style>
  :root {
    --navy: #2e4fa3;
    --royal: #1f6fc0;
    --sky: #0a8fd6;
    --ink: #1b1b1b;
    --paper: #ffffff;
    --stage: #e9ebef;
  }
  * { margin: 0; padding: 0; box-sizing: border-box; }
  html, body { width: 1200px; height: 900px; overflow: hidden; }
  body {
    background: var(--stage);
    font-family: "Lato", Arial, sans-serif;
    position: relative;
  }
  .card {
    position: absolute;
    left: 300px;
    width: 600px;
    height: 343px;
    overflow: hidden;
    box-shadow: 0 6px 18px rgba(0,0,0,0.18);
  }
  .brand {
    position: absolute;
    font-weight: 700;
    white-space: nowrap;
  }

  /* Back */
  .card-back {
    top: 70px;
    background: radial-gradient(ellipse at 62% 35%, var(--sky) 0%, var(--royal) 40%, var(--navy) 100%);
  }
  .card-back .brand {
    left: 0;
    right: 0;
    top: 128px;
    text-align: center;
    color: var(--paper);
    font-size: 42px;
  }
  .back-tab {
    position: absolute;
    left: 0;
    bottom: 0;
    width: 380px;
    height: 58px;
    background: var(--paper);
    border-top-right-radius: 40px;
    display: flex;
    align-items: center;
    padding-left: 50px;
  }
  .back-tab .web { color: var(--ink); font-size: 17px; letter-spacing: 0.3px; }

  /* Front */
  .card-front {
    top: 483px;
    background: var(--paper);
  }
  .card-front .brand {
    left: 40px;
    top: 40px;
    color: var(--navy);
    font-size: 34px;
  }
  .holder-name {
    position: absolute;
    right: 40px;
    top: 120px;
    color: var(--navy);
    font-size: 28px;
    font-weight: 700;
  }
  .rule {
    position: absolute;
    left: 40px;
    right: 40px;
    top: 162px;
    height: 1.5px;
    background: var(--navy);
  }
  .contacts {
    position: absolute;
    left: 40px;
    top: 178px;
    list-style: none;
    color: var(--ink);
    font-size: 17px;
    line-height: 26px;
  }
  .contacts li { display: flex; align-items: center; gap: 10px; }
  .contacts svg { width: 14px; height: 14px; fill: var(--navy); }
  .address {
    position: absolute;
    right: 40px;
    top: 178px;
    text-align: right;
    color: var(--ink);
    font-size: 19px;
    line-height: 24px;
  }
  .front-band {
    position: absolute;
    left: 0;
    right: 0;
    bottom: 0;
    height: 22px;
    background: var(--sky);
  }
  .front-tab {
    position: absolute;
    right: 0;
    bottom: 0;
    width: 340px;
    height: 52px;
    background: linear-gradient(90deg, var(--sky), var(--navy));
    border-top-left-radius: 34px;
    display: flex;
    align-items: center;
    padding-left: 32px;
  }
  .front-tab .web { color: var(--paper); font-size: 17px; letter-spacing: 0.3px; }
</style>
</head>
<body>
  <section class="card card-back" aria-label="Card back">
    <p class="brand">Harbourline Connect</p>
    <div class="back-tab"><span class="web">www.harbourlineconnect.com.au</span></div>
  </section>

  <section class="card card-front" aria-label="Card front">
    <p class="brand">Harbourline Connect</p>
    <p class="holder-name">Reid Callander</p>
    <div class="rule"></div>
    <ul class="contacts">
      <li>
        <svg viewBox="0 0 24 24" aria-hidden="true"><path d="M6.6 10.8a15.1 15.1 0 0 0 6.6 6.6l2.2-2.2c.3-.3.7-.4 1-.2 1.1.4 2.3.6 3.6.6.6 0 1 .4 1 1V20c0 .6-.4 1-1 1A17 17 0 0 1 3 4c0-.6.4-1 1-1h3.5c.6 0 1 .4 1 1 0 1.3.2 2.5.6 3.6.1.3 0 .7-.2 1z"/></svg>
        <span>040 555 0192</span>
      </li>
      <li>
        <svg viewBox="0 0 24 24" aria-hidden="true"><path d="M2 5h20v14H2z M2 5l10 8 10-8" fill="none" stroke="#2e4fa3" stroke-width="2.4"/></svg>
        <span>info@harbourlineconnect.com.au</span>
      </li>
    </ul>
    <p class="address">5820 Corran Lane<br>Ashby Park TX 78000</p>
    <div class="front-band"></div>
    <div class="front-tab"><span class="web">www.harbourlineconnect.com.au</span></div>
  </section>
</body>
</html>
```